SnackOrbit!!! A Vending Machine Business Looking for an attractive website.

We are a vending machine business in Northern Michigan. We have changed our name and have rebranded our company. We would like an attractive website that shares who we are, what services we provide, the products we offer in our machines, along with a form businesses can fill out to see if they are a good fit for our company. I would like to have a Home Page, About SnackOrbit, Why Choose SnackOrbit?, Products & Services, Contact Us (With a Login Option), and a page with a questionnaire for thos interested in getting a FREE Vending Machine.

Target Market(s)

Businesses, Campgrounds, Schools, and many more in Northern Michigan

Industry/Entity Type

Vending Machines

Coding

Coded - Design and coding required

Number of Pages Required

5+ page

Requirements
Must have
• An inviting and enticing Home Page. I want to get my potential clients engaged in our website.
Nice to have
• Possibly background photos from Northern Michigan
Should not have
• A corporate feel. I do not want a boring website.

```html
<!DOCTYPE html>
<html lang="en">
<head>
<meta charset="UTF-8">
<title>SnackOrbit — Vending in Northern Michigan</title>
<link rel="stylesheet" href="https://fonts.googleapis.com/css2?family=Poppins:wght@500;600;700;800&family=Open+Sans:wght@400;600&display=swap">
<style>
:root{
  --navy:#1d2160;
  --navy-deep:#141745;
  --green:#2f6b2a;
  --green-dark:#1f4a1c;
  --ink:#111111;
  --text:#555a66;
  --white:#ffffff;
  --card-shadow:0 8px 26px rgba(0,0,0,.14);
  --footer:#0b0b0b;
}
*{box-sizing:border-box;margin:0;padding:0}
html,body{width:1200px;height:3428px;overflow:hidden}
body{position:relative;background:var(--white);font-family:"Open Sans",Arial,sans-serif;color:var(--text)}
h1,h2,h3,.btn,.nav a,.brand{font-family:"Poppins",Arial,sans-serif}

/* header */
.site-header{position:absolute;top:0;left:0;width:1200px;height:160px;background:var(--white)}
.brand{position:absolute;display:flex;align-items:center;gap:10px;font-weight:800;color:var(--ink);font-size:34px}
.brand .mark{width:26px;height:26px;background:var(--navy);border-radius:50%}
.site-header .brand{left:110px;top:42px}
.header-actions{position:absolute;right:150px;top:28px;display:flex;gap:18px}
.nav{position:absolute;right:150px;top:92px;display:flex;gap:44px}
.nav a{color:var(--ink);text-decoration:none;font-size:19px;font-weight:500}
.btn{display:inline-block;border-radius:24px;padding:10px 30px;font-size:17px;font-weight:600;text-decoration:none;color:var(--white)}
.btn-green{background:var(--green)}
.btn-navy{background:var(--navy)}
.btn-white{background:var(--white);color:var(--navy)}

/* hero */
.hero-bg{position:absolute;top:160px;left:0;width:1200px;height:720px;background:linear-gradient(120deg,var(--navy-deep),var(--navy) 60%,#262b76)}
.hero-wave{position:absolute;left:0;top:740px;width:1200px;height:140px}
.hero-machine{position:absolute;left:150px;top:180px;width:310px;height:680px;border-radius:10px;background:linear-gradient(180deg,#3a3a3e,#1d1d20);box-shadow:0 12px 30px rgba(0,0,0,.35)}
.hero-machine::after{content:"";position:absolute;left:24px;top:40px;width:190px;height:500px;background:linear-gradient(180deg,#6d8fb5,#c9a24a 45%,#4f8a4a);border-radius:4px;opacity:.85}
.hero-title{position:absolute;left:580px;top:300px;width:540px;text-align:center;color:var(--white);font-size:64px;font-weight:800;line-height:1.08;letter-spacing:1px}
.hero-copy{position:absolute;left:600px;top:488px;width:500px;text-align:center;color:#e6e8f5;font-size:18px;line-height:1.6}
.hero-cta{position:absolute;left:940px;top:618px;font-size:15px;padding:8px 24px}

/* section headings */
.section-title{position:absolute;left:0;width:1200px;text-align:center;color:var(--ink);font-size:40px;font-weight:800;letter-spacing:1px}

/* services */
.services{position:absolute;top:1048px;left:148px;display:flex;gap:28px}
.service-card{position:relative;width:284px;height:392px;background:var(--white);border-radius:18px;box-shadow:var(--card-shadow);text-align:center}
.service-photo{height:170px;border-radius:18px 18px 0 0}
.photo-1{background:linear-gradient(135deg,#8a6b3f,#c7a35c,#5b7c44)}
.photo-2{background:linear-gradient(135deg,#5e6f86,#a3b1c4,#3d4c5f)}
.photo-3{background:linear-gradient(135deg,#6a8a58,#b8c08a,#4e6a3e)}
.service-icon{position:absolute;left:112px;top:138px;width:60px;height:60px;border-radius:12px;background:var(--green);display:flex;align-items:center;justify-content:center}
.service-card h3{margin-top:54px;font-size:18px;font-weight:700;color:var(--ink)}
.service-card p{margin:10px 26px 0;font-size:12.5px;line-height:1.5;height:57px}
.service-card .btn{margin-top:12px;font-size:13px;padding:7px 20px}
.carousel-dot{position:absolute;top:1236px;width:16px;height:16px;border-radius:50%;border:3px solid #bbb}

/* who we are */
.about-photo{position:absolute;left:112px;top:1672px;width:376px;height:376px;border-radius:50%;background:radial-gradient(circle at 40% 40%,#e8d9a0,#6fa0c8 55%,#3b6a3a);box-shadow:0 10px 30px rgba(0,0,0,.2)}
.about-title{position:absolute;left:600px;top:1664px;color:var(--ink);font-size:44px;font-weight:800;line-height:1.2}
.about-copy{position:absolute;left:600px;top:1740px;width:500px;font-size:16px;line-height:28px}
.about-btn{position:absolute;left:600px;top:1990px}

/* cta band */
.cta{position:absolute;top:2112px;left:0;width:1200px;height:408px;background:linear-gradient(180deg,var(--green-dark),var(--green) 50%,var(--green-dark));text-align:center;color:var(--white)}
.cta h2{margin-top:66px;font-size:40px;font-weight:800;line-height:1.3}
.cta p{margin:24px auto 0;width:720px;font-size:16px;line-height:1.6}
.cta-actions{margin-top:30px;display:flex;justify-content:center;gap:24px}

/* why choose */
.features{position:absolute;top:2712px;left:88px;display:flex;gap:40px}
.feature-card{width:232px;height:388px;background:var(--white);border-radius:16px;box-shadow:var(--card-shadow);text-align:center;padding-top:36px}
.feature-icon{width:72px;height:72px;border-radius:50%;background:var(--navy);margin:0 auto;display:flex;align-items:center;justify-content:center}
.feature-card h3{margin:22px 16px 0;font-size:16.5px;font-weight:800;color:var(--ink);line-height:1.3}
.feature-card p{margin:16px 22px 0;font-size:13px;line-height:1.6}

/* footer */
.site-footer{position:absolute;top:3200px;left:0;width:1200px;height:228px;background:var(--footer);text-align:center;color:var(--white)}
.site-footer .brand{left:50%;transform:translateX(-50%);top:36px;color:var(--white)}
.site-footer .brand .mark{background:var(--white)}
.footer-nav{position:absolute;top:108px;left:0;width:1200px;display:flex;justify-content:center;gap:34px}
.footer-nav a{color:var(--white);text-decoration:none;font-size:15px;font-family:"Poppins",Arial,sans-serif}
.social{position:absolute;top:142px;left:587px;width:26px;height:26px;border-radius:50%;background:var(--white)}
.copyright{position:absolute;top:184px;left:0;width:1200px;font-size:14px}
.lang{position:absolute;right:40px;top:186px;font-size:13px}
</style>
</head>
<body>

<header class="site-header">
  <div class="brand"><span class="mark"></span>SnackOrbit</div>
  <div class="header-actions">
    <a class="btn btn-green" href="#">Contact Us</a>
    <a class="btn btn-navy" href="#">Get Started</a>
  </div>
  <nav class="nav">
    <a href="#">Home</a>
    <a href="#">About SnackOrbit</a>
    <a href="#">Why Choose Us?</a>
    <a href="#">Products &amp; Services</a>
  </nav>
</header>

<div class="hero-bg"></div>
<svg class="hero-wave" viewBox="0 0 1200 140" preserveAspectRatio="none" aria-hidden="true">
  <path d="M0 20 C300 110 700 120 1200 0 L1200 140 L0 140Z" fill="#ffffff"/>
  <path d="M0 20 C300 110 700 120 1200 0 L1200 40 C700 150 300 140 0 60Z" fill="#2f6b2a"/>
</svg>
<div class="hero-machine" role="img" aria-label="Stocked snack vending machine"></div>
<h1 class="hero-title">WELCOME TO<br>SNACKORBIT</h1>
<p class="hero-copy">We're not just about vending machines; we're your culinary companions, your flavor curators, and your secret stash of happiness.</p>
<a class="btn btn-green hero-cta" href="#">Contact Us</a>

<h2 class="section-title" style="top:946px">SERVICES WE PROVIDE</h2>
<span class="carousel-dot" style="left:82px"></span>
<span class="carousel-dot" style="left:1100px;border-color:#333"></span>
<div class="services">
  <article class="service-card">
    <div class="service-photo photo-1" role="img" aria-label="Vending machine placed in a break room"></div>
    <div class="service-icon"><svg width="30" height="34" viewBox="0 0 30 34"><rect x="3" y="2" width="24" height="30" rx="2" fill="none" stroke="#fff" stroke-width="3"/><rect x="8" y="7" width="10" height="16" fill="#fff"/><rect x="21" y="9" width="3" height="6" fill="#fff"/></svg></div>
    <h3>VENDING MACHINE</h3>
    <p>Modern machines stocked with snacks and drinks, placed where your people gather.</p>
    <a class="btn btn-navy" href="#">Read More</a>
  </article>
  <article class="service-card">
    <div class="service-photo photo-2" role="img" aria-label="Technician repairing a vending machine"></div>
    <div class="service-icon"><svg width="32" height="32" viewBox="0 0 32 32"><path d="M6 26 L20 12" stroke="#fff" stroke-width="4" stroke-linecap="round"/><circle cx="22" cy="10" r="6" fill="none" stroke="#fff" stroke-width="3"/></svg></div>
    <h3>REPAIR</h3>
    <p>Fast, friendly repairs that keep your machine running and your customers happy.</p>
    <a class="btn btn-navy" href="#">Read More</a>
  </article>
  <article class="service-card">
    <div class="service-photo photo-3" role="img" aria-label="Crew installing a machine at a business"></div>
    <div class="service-icon"><svg width="32" height="32" viewBox="0 0 32 32"><circle cx="16" cy="16" r="9" fill="none" stroke="#fff" stroke-width="4" stroke-dasharray="5 3"/><circle cx="16" cy="16" r="4" fill="#fff"/></svg></div>
    <h3>INSTALL &amp; SERVICE</h3>
    <p>We deliver, install and service every machine so you never lift a finger.</p>
    <a class="btn btn-navy" href="#">Read More</a>
  </article>
</div>

<div class="about-photo" role="img" aria-label="Shelves of colorful bottled drinks"></div>
<h2 class="about-title">WHO WE ARE</h2>
<p class="about-copy">We're not just about vending machines; we're your culinary companions, your flavor curators, and your secret stash of happiness. We're the ones who believe that a vending machine isn't just a metal box; it's a portal to delight. Our mission? To transform mundane moments into enjoyable bites. Dana and Nolan, the dynamic duo behind SnackOrbit, have a passion for all things tasty. With backgrounds in sales and a penchant for personal connections, they've transformed the vending experience into an art form.</p>
<a class="btn btn-navy about-btn" href="#">Read More</a>

<section class="cta" role="img" aria-label="Green-toned photo of snack shelves behind the call to action">
  <h2>READY TO<br>EXPERIENCE THE SNACKORBIT DIFFERENCE</h2>
  <p>Sign up now and let's connect. Taste the future of snacking firsthand! Contact us today and explore how our vending magic can elevate your space!</p>
  <div class="cta-actions">
    <a class="btn btn-navy" href="#">Sign Up</a>
    <a class="btn btn-white" href="#">Contact Us</a>
  </div>
</section>

<h2 class="section-title" style="top:2612px">WHY CHOOSE SNACKORBIT?</h2>
<div class="features">
  <article class="feature-card">
    <div class="feature-icon"><svg width="34" height="30" viewBox="0 0 34 30"><path d="M17 28 C4 19 1 13 1 8 A7 7 0 0 1 17 5 A7 7 0 0 1 33 8 C33 13 30 19 17 28Z" fill="#fff"/></svg></div>
    <h3>LOCAL LOVE</h3>
    <p>We celebrate the heart of Northern Michigan by partnering with local suppliers and nearby favorites.</p>
  </article>
  <article class="feature-card">
    <div class="feature-icon"><svg width="36" height="36" viewBox="0 0 36 36"><circle cx="18" cy="18" r="15" fill="none" stroke="#fff" stroke-width="3"/><circle cx="12" cy="14" r="2" fill="#fff"/><circle cx="24" cy="14" r="2" fill="#fff"/><path d="M10 21 Q18 29 26 21" fill="none" stroke="#fff" stroke-width="3"/></svg></div>
    <h3>UNLEASH YOUR CRAVINGS</h3>
    <p>SnackOrbit isn't bound by one snack list. We're tailored to your crowd, from classics to new finds.</p>
  </article>
  <article class="feature-card">
    <div class="feature-icon"><svg width="30" height="36" viewBox="0 0 30 36"><circle cx="15" cy="13" r="10" fill="none" stroke="#fff" stroke-width="3"/><path d="M9 21 L6 34 L15 29 L24 34 L21 21" fill="#fff"/></svg></div>
    <h3>QUALITY<br>MEETS CONVENIENCE</h3>
    <p>Snacks that meet our standard for freshness, served around the clock right where you need them.</p>
  </article>
  <article class="feature-card">
    <div class="feature-icon"><svg width="30" height="34" viewBox="0 0 30 34"><path d="M15 2 L28 7 V16 C28 24 22 30 15 32 C8 30 2 24 2 16 V7Z" fill="#fff"/><path d="M9 17 L13 21 L21 12" fill="none" stroke="#1d2160" stroke-width="3"/></svg></div>
    <h3>PANDEMIC PROOF &amp;<br>RECESSION READY</h3>
    <p>Touch-free payment and reliable service keep SnackOrbit steady through any season.</p>
  </article>
</div>

<footer class="site-footer">
  <div class="brand"><span class="mark"></span>SnackOrbit</div>
  <nav class="footer-nav">
    <a href="#">Home</a>
    <a href="#">About SnackOrbit</a>
    <a href="#">Why Choose Us?</a>
    <a href="#">Products &amp; Services</a>
    <a href="#">Contact Us</a>
  </nav>
  <span class="social" aria-hidden="true"></span>
  <p class="copyright">(C) Copyright 2024 | All Rights Reserved</p>
  <span class="lang">CTA</span>
</footer>

</body>
</html>
```